Landscape Construction and Design Company

We are a landscape construction and design company from New Jersey. We design and install landscapes and hardscapes for residential properties. The name of the company is Belwick's Landscape and Design LLC. We specialize mostly in planting trees and stone work, some water features. We would like to see design themes that include a tree or trees and a stone walkway or wall. We like earth tone colors. We like traditional to modern designs.

Target Market(s)

Homeowners

Industry/Entity Type

Landscape

Contact Information for Business Card

Nature themed design, earth tone colors, space for company name, address, phone numbers, email and website address

Logo Text

No text

Font styles to use
Serif

Colors

Designer to choose colors to be used in the design.

Requirements
Must have
• A tree or trees, similar to the ones uploaded in my supporting images
Nice to have
• I like trees similar to those in my uploaded supporting images. I like artistic, nature theme, earth tone colors
Should not have
• Pictures of real landscapes, cartoon looking logo or objects

```html
<!DOCTYPE html>
<html lang="en">
<head>
<meta charset="utf-8">
<title>Belwick's Landscape and Design LLC — Business Card</title>
<link rel="stylesheet" href="https://fonts.googleapis.com/css2?family=Source+Sans+3:wght@400;600&display=swap">
<style>
  :root {
    --bg: #e9e7e2;
    --card-white: #ffffff;
    --leaf-green: #64a02b;
    --brand-green: #4f9a2a;
    --bark-brown: #7b2b2d;
    --text-light: #ffffff;
  }
  * { margin: 0; padding: 0; box-sizing: border-box; }
  html, body {
    width: 1200px; height: 900px; overflow: hidden;
    background: var(--bg);
  }
  .canvas { position: relative; width: 1200px; height: 900px; }

  .card {
    position: absolute; overflow: hidden;
    box-shadow: 0 6px 18px rgba(0,0,0,0.18);
  }
  .card--front { left: 178px; top: 73px; width: 588px; height: 365px; background: var(--card-white); }
  .card--back { left: 388px; top: 505px; width: 567px; height: 352px; background: var(--leaf-green); }

  .front-shapes { position: absolute; inset: 0; }

  .brand {
    position: absolute; left: 108px; top: 34px;
    display: flex; align-items: center; gap: 20px;
  }
  .brand__dot {
    width: 120px; height: 120px; border-radius: 50%;
    background: var(--brand-green); flex: none;
  }
  .brand__name {
    width: 250px;
    font-family: "Source Sans 3", Arial, sans-serif; font-weight: 600;
    font-size: 27px; line-height: 1.15; color: var(--brand-green);
  }

  .person {
    position: absolute; right: 326px; top: 256px; text-align: right;
    font-family: "Source Sans 3", Arial, sans-serif; color: var(--text-light);
  }
  .person__name { font-size: 19px; font-weight: 600; letter-spacing: 0.3px; line-height: 1.1; }
  .person__title { font-size: 16px; font-weight: 400; margin-top: 2px; }

  .contacts {
    position: absolute; left: 292px; top: 247px; list-style: none;
    font-family: "Source Sans 3", Arial, sans-serif; font-size: 16px;
    color: var(--text-light); line-height: 21.5px;
  }
  .contacts li { display: flex; align-items: center; gap: 6px; }
  .contacts svg { width: 11px; height: 11px; fill: var(--text-light); flex: none; }

  .address {
    position: absolute; left: 90px; top: 320px;
    font-family: "Source Sans 3", Arial, sans-serif; font-size: 16px;
    color: var(--text-light);
  }

  .back-brand {
    position: absolute; left: 0; right: 0; top: 48px;
    display: flex; flex-direction: column; align-items: center; gap: 20px;
  }
  .back-brand__dot {
    width: 150px; height: 150px; border-radius: 50%;
    background: var(--bark-brown);
  }
  .back-brand__name {
    font-family: "Source Sans 3", Arial, sans-serif; font-weight: 600;
    font-size: 21px; color: var(--text-light);
  }
  .services {
    position: absolute; left: 0; right: 0; top: 293px; text-align: center;
    font-family: "Source Sans 3", Arial, sans-serif; font-size: 17px;
    color: var(--text-light); letter-spacing: 0.2px;
  }
</style>
</head>
<body>
<main class="canvas">

  <section class="card card--front" aria-label="Business card front">
    <svg class="front-shapes" width="588" height="365" viewBox="0 0 588 365">
      <polygon points="0,196 400,196 381,221 0,221" fill="var(--bark-brown)"/>
      <polygon points="0,226 388,226 416,189 588,189 588,365 0,365" fill="var(--leaf-green)"/>
    </svg>

    <div class="brand">
      <span class="brand__dot"></span>
      <p class="brand__name">Belwick's Landscape and Design LLC</p>
    </div>

    <div class="person">
      <p class="person__name">MARCUS HALE</p>
      <p class="person__title">Managing Director</p>
    </div>

    <ul class="contacts">
      <li>
        <svg viewBox="0 0 24 24"><path d="M6.6 10.8a15.1 15.1 0 0 0 6.6 6.6l2.2-2.2a1 1 0 0 1 1-.25 11.4 11.4 0 0 0 3.6.57 1 1 0 0 1 1 1V20a1 1 0 0 1-1 1A17 17 0 0 1 3 4a1 1 0 0 1 1-1h3.5a1 1 0 0 1 1 1c0 1.25.2 2.45.57 3.57a1 1 0 0 1-.25 1z"/></svg>
        044-987 654 321
      </li>
      <li>
        <svg viewBox="0 0 24 24"><path d="M2 5h20v14H2z M4 7v.4l8 5 8-5V7l-8 5z" fill-rule="evenodd"/></svg>
        hello@belwickland.com
      </li>
      <li>
        <svg viewBox="0 0 24 24"><path d="M12 2a10 10 0 1 0 0 20 10 10 0 0 0 0-20zm0 2c.9 0 2.2 2 2.7 5H9.3C9.8 6 11.1 4 12 4zM4.3 11h3a18 18 0 0 0 0 2h-3a8 8 0 0 1 0-2zm5 0h5.4a16 16 0 0 1 0 2H9.3a16 16 0 0 1 0-2zm7.4 0h3a8 8 0 0 1 0 2h-3a18 18 0 0 0 0-2zM9.3 15h5.4c-.5 3-1.8 5-2.7 5s-2.2-2-2.7-5z"/></svg>
        www.belwickland.com
      </li>
    </ul>

    <p class="address">48 Orchard Lane, Morristown, New Jersey, 07960.</p>
  </section>

  <section class="card card--back" aria-label="Business card back">
    <div class="back-brand">
      <span class="back-brand__dot"></span>
      <p class="back-brand__name">Belwick's Landscape and Design LLC</p>
    </div>
    <p class="services">PLANTING TREES | STONE WORK | WATER FEATURES</p>
  </section>

</main>
</body>
</html>
```